Company identity deisgn should support 2 languages

I would like to get our company identity design
This includes the following only
Business Cards 2 languages Arabic and English
Email signature
Letterhead
Linkedin profile images
Attached is the logo in Ai format

Requirements
Must have
• For business card
Must have
Name and Adrees in arabic
Name and Address in english
You might use both side of the card
Should not have
• Any pictures other than the logo

```html
<!DOCTYPE html>
<html lang="en">
<head>
<meta charset="utf-8">
<title>Northwind Cognitive – Business Cards</title>
<link rel="stylesheet" href="https://fonts.googleapis.com/css2?family=Montserrat:wght@400;500;600&family=Cairo:wght@500;700&display=swap">
<style>
  :root {
    --page: #e9eaec;
    --card: #ffffff;
    --brand-blue: #0f76bf;
    --ink-light: #ffffff;
  }
  * { margin: 0; padding: 0; box-sizing: border-box; }
  html, body { width: 1200px; height: 1200px; overflow: hidden; background: var(--page); }
  .sheet {
    position: relative; width: 1200px; height: 1200px;
    font-family: "Montserrat", Arial, sans-serif;
  }
  .card {
    position: absolute; left: 200px; width: 800px; height: 456px;
    background: var(--card); border-radius: 30px; overflow: hidden;
    box-shadow: 0 18px 30px rgba(0,0,0,0.25);
  }
  .card--english { top: 100px; }
  .card--arabic { top: 640px; }
  .card__band { position: absolute; inset: 0; width: 800px; height: 456px; }
  .brand {
    position: absolute; left: 56px; top: 118px;
    display: flex; align-items: center; gap: 14px;
  }
  .brand__dot { width: 46px; height: 46px; border-radius: 50%; background: var(--brand-blue); }
  .brand__name {
    font-size: 25px; font-weight: 500; letter-spacing: 0.5px; color: var(--brand-blue);
    text-transform: uppercase;
  }
  .details {
    position: absolute; right: 36px; top: 236px; text-align: right; color: var(--ink-light);
  }
  .details__name { font-size: 25px; font-weight: 600; letter-spacing: 0.3px; line-height: 32px; }
  .details__role { font-size: 17px; font-weight: 400; line-height: 22px; margin-bottom: 18px; }
  .contact { list-style: none; }
  .contact__item {
    display: flex; justify-content: flex-end; align-items: center; gap: 10px;
    font-size: 17px; line-height: 23px;
  }
  .contact__icon { width: 15px; height: 15px; fill: var(--ink-light); flex: none; }
  .details__address { font-size: 17px; margin-top: 6px; letter-spacing: 0.2px; }
  .card--arabic .details__name,
  .card--arabic .details__role,
  .card--arabic .details__address { font-family: "Cairo", "Montserrat", sans-serif; }
  .card--arabic .details__name { font-size: 27px; font-weight: 700; }
  .card--arabic .details__role { font-size: 19px; font-weight: 700; }
  .card--arabic .contact__item { font-size: 19px; }
</style>
</head>
<body>
<main class="sheet">

  <svg width="0" height="0" style="position:absolute">
    <defs>
      <symbol id="icon-phone" viewBox="0 0 16 16"><path d="M3.6 1.2l2.3 2.6-1.2 1.6c.9 2 2.4 3.6 4.6 4.8l1.6-1.2 2.7 2.2-1.3 2.4C7.5 13.4 2.7 8.6 1.4 3.3z"/></symbol>
      <symbol id="icon-mobile" viewBox="0 0 16 16"><path d="M4 1h8v14H4zM5.4 2.6v9.6h5.2V2.6z"/></symbol>
      <symbol id="icon-mail" viewBox="0 0 16 16"><path d="M1 4h14v9H1zM2.4 5.2 8 9.2l5.6-4z" fill-rule="evenodd"/></symbol>
      <symbol id="icon-globe" viewBox="0 0 16 16"><path d="M8 1a7 7 0 1 0 0 14A7 7 0 0 0 8 1zm-2 3 2 1-1 2 2 1v2l-2 2-1-3-2-1 1-3zm4 0 2 1 1 3-2-1z" fill-rule="evenodd"/></symbol>
    </defs>
  </svg>

  <!-- English side -->
  <section class="card card--english">
    <svg class="card__band" viewBox="0 0 800 456" role="img" aria-label="Decorative brand-blue wave band">
      <path d="M0 400 C 220 460 400 380 480 220 C 540 110 680 100 800 120 L800 456 L0 456 Z" fill="var(--brand-blue)"/>
    </svg>
    <div class="brand">
      <span class="brand__dot"></span>
      <span class="brand__name">Northwind Cognitive</span>
    </div>
    <div class="details">
      <div class="details__name">DANIEL HARPER</div>
      <div class="details__role">President</div>
      <ul class="contact">
        <li class="contact__item">555-240-1187 <svg class="contact__icon"><use href="#icon-phone"/></svg></li>
        <li class="contact__item">555-380-6624 <svg class="contact__icon"><use href="#icon-mobile"/></svg></li>
        <li class="contact__item">hello@northwindcognitive.com <svg class="contact__icon"><use href="#icon-mail"/></svg></li>
        <li class="contact__item">www.northwindcognitive.com <svg class="contact__icon"><use href="#icon-globe"/></svg></li>
      </ul>
      <div class="details__address">1420 Maple Court, Juneau, Alaska 99801</div>
    </div>
  </section>

  <!-- Arabic side -->
  <section class="card card--arabic">
    <svg class="card__band" viewBox="0 0 800 456" role="img" aria-label="Decorative brand-blue wave band">
      <path d="M0 400 C 220 460 400 380 480 220 C 540 110 680 100 800 120 L800 456 L0 456 Z" fill="var(--brand-blue)"/>
    </svg>
    <div class="brand">
      <span class="brand__dot"></span>
      <span class="brand__name">Northwind Cognitive</span>
    </div>
    <div class="details">
      <div class="details__name" dir="rtl">دانيال هاربر</div>
      <div class="details__role" dir="rtl">رئيس</div>
      <ul class="contact">
        <li class="contact__item">555-240-1187 <svg class="contact__icon"><use href="#icon-phone"/></svg></li>
        <li class="contact__item">555-380-6624 <svg class="contact__icon"><use href="#icon-mobile"/></svg></li>
        <li class="contact__item">hello@northwindcognitive.com <svg class="contact__icon"><use href="#icon-mail"/></svg></li>
        <li class="contact__item">www.northwindcognitive.com <svg class="contact__icon"><use href="#icon-globe"/></svg></li>
      </ul>
      <div class="details__address" dir="rtl">1420 شارع مابل، جونو، ألاسكا 99801</div>
    </div>
  </section>

</main>
</body>
</html>
```